Oil Field Service company needs professional business cards

Looking to clean up our current company business cards and look a little more professional. Brenwick Casing Services is a US based company that services the oil field. We deal with engineers, managers and oil rigs....................................................................................................................................................................................................................................................................................................................................................................................................

Target Market(s)

Oil and Gas professionals

Industry/Entity Type

Oil And Gas

Contact Information for Business Card

See attached photo as example

Font styles to use
Sans Serif

Colors
ec1f27

Requirements
Must have
• Company Logo, Name, Title, Cell, Office, Fax, Email.
• See attached photo
Nice to have
• External CRT, Internal CRT, Casing Crews, Torque Turn, Laydown Machine
Should not have
• Do not introduce any new pictures and keep it professional looking

```html
<!DOCTYPE html>
<html lang="en">
<head>
<meta charset="utf-8">
<title>Brenwick Casing Services – Business Card</title>
<link href="https://fonts.googleapis.com/css2?family=Source+Sans+3:wght@400;600;700&display=swap" rel="stylesheet">
<style>
  :root {
    --brand-red: #e21b25;
    --ink: #3d4750;
    --paper: #ffffff;
    --backdrop: #ece8e4;
    --font: "Source Sans 3", "Helvetica Neue", Arial, sans-serif;
  }
  * { box-sizing: border-box; margin: 0; padding: 0; }
  html, body { width: 1200px; height: 900px; overflow: hidden; }
  body { background: var(--backdrop); font-family: var(--font); position: relative; }

  .card { position: absolute; overflow: hidden; background: var(--paper); box-shadow: 0 6px 18px rgba(0,0,0,.18); }

  /* Front */
  .card-front { left: 77px; top: 34px; width: 589px; height: 364px; }
  .card-front .brand-zone { position: absolute; left: 0; top: 0; width: 100%; height: 156px; }
  .card-front .info-zone { position: absolute; left: 0; top: 156px; width: 100%; height: 208px; background: var(--brand-red); color: var(--paper); }

  .wordmark { color: var(--ink); font-weight: 700; line-height: 1; text-transform: uppercase; }
  .wordmark .name { display: block; font-size: 42px; letter-spacing: 4px; }
  .wordmark .sub { display: block; font-size: 14px; letter-spacing: 3.4px; margin-top: 18px; }
  .card-front .wordmark { position: absolute; left: 33px; top: 50px; }

  .person-name { position: absolute; left: 32px; top: 15px; font-size: 19px; font-weight: 700; line-height: 1.2; }
  .person-title { position: absolute; left: 32px; top: 39px; font-size: 16px; line-height: 1.2; }

  .contact-list { position: absolute; left: 32px; top: 70px; list-style: none; }
  .contact-list li { display: flex; align-items: center; height: 21px; font-size: 16px; }
  .contact-list svg { width: 12px; height: 12px; margin-right: 10px; fill: var(--paper); flex: none; }

  .service-line { position: absolute; left: 30px; top: 164px; font-size: 17px; line-height: 22px; white-space: nowrap; }

  /* Back */
  .card-back { left: 388px; top: 505px; width: 567px; height: 352px; background: var(--brand-red); }
  .card-back .white-band { position: absolute; left: 0; top: 110px; width: 100%; height: 131px; background: var(--paper); display: flex; align-items: center; justify-content: center; text-align: center; }
  .card-back .wordmark .name { font-size: 40px; }
  .card-back .wordmark .sub { margin-top: 16px; }
</style>
</head>
<body>

  <section class="card card-front" aria-label="Business card front">
    <div class="brand-zone">
      <div class="wordmark">
        <span class="name">Brenwick</span>
        <span class="sub">Casing Services</span>
      </div>
    </div>
    <div class="info-zone">
      <p class="person-name">Cody Harlan</p>
      <p class="person-title">Area Manager</p>
      <ul class="contact-list">
        <li>
          <svg viewBox="0 0 24 24" aria-hidden="true"><path d="M6.6 10.8a15.1 15.1 0 0 0 6.6 6.6l2.2-2.2c.3-.3.7-.4 1-.2 1.1.4 2.3.6 3.6.6.6 0 1 .4 1 1V20c0 .6-.4 1-1 1A17 17 0 0 1 3 4c0-.6.4-1 1-1h3.5c.6 0 1 .4 1 1 0 1.3.2 2.5.6 3.6.1.3 0 .7-.2 1z"/></svg>
          (405) 555-0142
        </li>
        <li>
          <svg viewBox="0 0 24 24" aria-hidden="true"><path d="M7 1h10a2 2 0 0 1 2 2v18a2 2 0 0 1-2 2H7a2 2 0 0 1-2-2V3a2 2 0 0 1 2-2zm0 3v14h10V4zm5 15.5a1 1 0 1 0 0 2 1 1 0 0 0 0-2z"/></svg>
          (405) 555-0187
        </li>
        <li>
          <svg viewBox="0 0 24 24" aria-hidden="true"><path d="M7 2h8l3 3v4h1a3 3 0 0 1 3 3v8a2 2 0 0 1-2 2H4a2 2 0 0 1-2-2v-8a3 3 0 0 1 3-3h2zm2 2v5h7V6h-2V4zm-3 9v2h3v-2zm5 0v2h3v-2zm5 0v2h3v-2zm-10 4v2h3v-2zm5 0v2h3v-2zm5 0v2h3v-2z"/></svg>
          (405) 555-0163
        </li>
        <li>
          <svg viewBox="0 0 24 24" aria-hidden="true"><path d="M2 5h20v14H2zm2 2v.5l8 5 8-5V7zm0 2.8V17h16V9.8l-8 5z"/></svg>
          cody.harlan@brenwickcasing.com
        </li>
      </ul>
      <p class="service-line">Laydown Machine | Casing Crew | Mud Tool | Torque Turn</p>
    </div>
  </section>

  <section class="card card-back" aria-label="Business card back">
    <div class="white-band">
      <div class="wordmark">
        <span class="name">Brenwick</span>
        <span class="sub">Casing Services</span>
      </div>
    </div>
  </section>

</body>
</html>
```